New LLC consulting company needs a business card design

I need a business card design for new company in Alexandria Virginia called TK Verdane Consulting LLC. The company is focused on consulting for defense and national security issues with expertise in nuclear and space topics. I would like to see designs that are simple and I am open to colors except for brown.

Target Market(s)

All businesses that are seeking consulting help

Industry/Entity Type

Consulting

Contact Information for Business Card

Name of company - TK Verdane Consulting LLC; name (Delia Pratt) President; email: prattdq47@mailvessa.com; Phone: 703-555-0142

Requirements
Must have
• The details described above
Nice to have
• I'm open to all ideas
Should not have
• No brown

```html
<!DOCTYPE html>
<html lang="en">
<head>
<meta charset="utf-8">
<title>Delia Pratt – TK Verdane Consulting LLC</title>
<link href="https://fonts.googleapis.com/css2?family=Montserrat:wght@400;500;600&display=swap" rel="stylesheet">
<style>
  :root {
    --backdrop: #1f1f1f;
    --card: #ffffff;
    --accent: #1e3a64;
    --ink: #2e2e2e;
  }
  * { margin: 0; padding: 0; box-sizing: border-box; }
  html, body {
    width: 1200px;
    height: 1059px;
    overflow: hidden;
    background: var(--backdrop);
  }
  .business-card {
    position: absolute;
    left: 50px;
    top: 215px;
    width: 1100px;
    height: 629px;
    background: var(--card);
    border-radius: 28px;
    font-family: "Montserrat", sans-serif;
  }
  .company {
    position: absolute;
    left: 58px;
    top: 86px;
    display: flex;
    align-items: center;
    gap: 16px;
  }
  .company-mark {
    width: 26px;
    height: 26px;
    border-radius: 50%;
    background: var(--accent);
    flex: none;
  }
  .company-name {
    font-size: 34px;
    font-weight: 600;
    line-height: 1;
    color: var(--accent);
    letter-spacing: 0.3px;
  }
  .holder-name {
    position: absolute;
    left: 58px;
    top: 352px;
    font-size: 54px;
    font-weight: 600;
    line-height: 1;
    color: var(--accent);
    letter-spacing: 0.2px;
  }
  .holder-title {
    position: absolute;
    left: 58px;
    top: 425px;
    font-size: 29px;
    font-weight: 400;
    line-height: 1;
    color: var(--ink);
    letter-spacing: 0.5px;
  }
  .divider {
    position: absolute;
    left: 60px;
    top: 489px;
    width: 640px;
    height: 5px;
  }
  .contact-row {
    position: absolute;
    left: 60px;
    top: 522px;
    display: flex;
    align-items: center;
    gap: 34px;
    font-size: 28px;
    font-weight: 400;
    color: var(--ink);
    letter-spacing: 0.4px;
    white-space: nowrap;
  }
  .contact-item {
    display: flex;
    align-items: center;
    gap: 12px;
  }
  .contact-icon { fill: var(--accent); flex: none; }
</style>
</head>
<body>
  <div class="business-card">
    <div class="company">
      <span class="company-mark" aria-hidden="true"></span>
      <span class="company-name">TK Verdane Consulting LLC</span>
    </div>

    <h1 class="holder-name">Delia Pratt</h1>
    <p class="holder-title">President</p>

    <svg class="divider" viewBox="0 0 640 5" preserveAspectRatio="none" aria-hidden="true">
      <defs>
        <linearGradient id="dividerFade" x1="0" x2="1" y1="0" y2="0">
          <stop offset="0" stop-color="#1e3a64"/>
          <stop offset="0.55" stop-color="#1e3a64"/>
          <stop offset="1" stop-color="#1e3a64" stop-opacity="0.25"/>
        </linearGradient>
      </defs>
      <path d="M0 0.5 L640 1.8 L640 2.6 L0 4.5 Z" fill="url(#dividerFade)"/>
    </svg>

    <div class="contact-row">
      <div class="contact-item">
        <svg class="contact-icon" width="23" height="16" viewBox="0 0 23 16" aria-hidden="true">
          <path d="M0 0h23v1.2L11.5 9 0 1.2z"/>
          <path d="M0 3l7.5 5.1L0 14.2zM23 3l-7.5 5.1L23 14.2zM8.8 9l2.7 1.9L14.2 9 23 16H0z"/>
        </svg>
        <span class="contact-email">prattdq47@mailvessa.com</span>
      </div>
      <div class="contact-item">
        <svg class="contact-icon" width="26" height="26" viewBox="0 0 24 24" aria-hidden="true">
          <path d="M6.6 10.8c1.4 2.8 3.8 5.1 6.6 6.6l2.2-2.2c.3-.3.7-.4 1-.2 1.1.4 2.3.6 3.6.6.6 0 1 .4 1 1V20c0 .6-.4 1-1 1C10.6 21 3 13.4 3 4c0-.6.4-1 1-1h3.5c.6 0 1 .4 1 1 0 1.3.2 2.5.6 3.6.1.3 0 .7-.2 1z"/>
          <path d="M14 2.5a8 8 0 0 1 7.5 7.5h-1.6A6.4 6.4 0 0 0 14 4.1zM14 6a4.5 4.5 0 0 1 4 4h-1.6A3 3 0 0 0 14 7.6z"/>
        </svg>
        <span class="contact-phone">703-555-0142</span>
      </div>
    </div>
  </div>
</body>
</html>
```